Business Card Design

Business Card for professional consulting firm working with large financial institutions.

Target Market(s)

Executive buyers

Industry/Entity Type

Banking

Contact Information for Business Card

Mild creativity wanted. Not boring, but do elaborate artwork.

Font styles to use
Serif
Sans Serif

Colors

Designer to choose colors to be used in the design.

Requirements
Must have
• Standard business card features - company name, individual name, telephone, website, email, locations.
Nice to have
• Two colors
Should not have
• too many colors, fancy printing, cartoons.

```html
<!DOCTYPE html>
<html lang="en">
<head>
<meta charset="utf-8">
<title>Northvale Business Card</title>
<link href="https://fonts.googleapis.com/css2?family=Roboto:wght@400;500&display=swap" rel="stylesheet">
<style>
  :root {
    --backdrop: #e6e3df;
    --card-light: #f3f3f3;
    --card-dark: #1b1c1e;
    --panel-black: #000000;
    --accent-grey: #bdbdbd;
    --text-white: #ffffff;
    --text-muted: #b5b5b5;
    --text-logo-dark: #3a3a3a;
  }
  * { margin: 0; padding: 0; box-sizing: border-box; }
  html, body {
    width: 1200px;
    height: 960px;
    overflow: hidden;
    background: var(--backdrop);
    font-family: "Roboto", Arial, sans-serif;
  }
  .canvas { position: relative; width: 1200px; height: 960px; }

  .card {
    position: absolute;
    width: 600px;
    height: 343px;
    box-shadow: 0 2px 6px rgba(0,0,0,0.25);
  }
  .card--front { left: 314px; top: 113px; background: var(--card-light); }
  .card--back  { left: 311px; top: 472px; background: var(--card-dark); }

  .accent-bar {
    position: absolute;
    left: 0; top: 83px;
    width: 14px; height: 173px;
    background: var(--accent-grey);
  }
  .brand-name {
    position: absolute;
    font-weight: 400;
    letter-spacing: 0.5px;
    white-space: nowrap;
  }
  .card--front .brand-name {
    left: 44px; top: 148px;
    font-size: 30px;
    color: var(--text-logo-dark);
  }
  .card--back .brand-name {
    left: 0; right: 0; top: 145px;
    text-align: center;
    font-size: 38px;
    color: var(--text-white);
  }

  .contact-panel {
    position: absolute;
    left: 332px; top: 83px;
    width: 268px; height: 173px;
    background: var(--panel-black);
    color: var(--text-white);
    padding: 13px 0 0 33px;
  }
  .person-name { font-size: 21px; font-weight: 500; line-height: 26px; }
  .person-title { font-size: 14px; color: var(--text-muted); line-height: 16px; margin-bottom: 6px; }
  .address { font-size: 14px; line-height: 18px; margin-bottom: 8px; }
  .contact-list { list-style: none; font-size: 14px; line-height: 19px; }
  .contact-list li { display: flex; align-items: center; gap: 8px; }
  .contact-list svg { width: 12px; height: 12px; fill: var(--text-muted); flex: none; }
</style>
</head>
<body>
<div class="canvas">

  <section class="card card--front">
    <div class="accent-bar"></div>
    <div class="brand-name">northvale</div>
    <div class="contact-panel">
      <div class="person-name">DANIEL REYES</div>
      <div class="person-title">CEO/FOUNDER</div>
      <div class="address">2140 Harbor Street<br>Juneau, Alaska 99801</div>
      <ul class="contact-list">
        <li>
          <svg viewBox="0 0 24 24" aria-hidden="true"><path d="M6.6 10.8a15.1 15.1 0 0 0 6.6 6.6l2.2-2.2a1 1 0 0 1 1-.25 11.4 11.4 0 0 0 3.6.57 1 1 0 0 1 1 1V20a1 1 0 0 1-1 1A17 17 0 0 1 3 4a1 1 0 0 1 1-1h3.5a1 1 0 0 1 1 1c0 1.25.2 2.45.57 3.57a1 1 0 0 1-.25 1z"/></svg>
          555 210 4783
        </li>
        <li>
          <svg viewBox="0 0 24 24" aria-hidden="true"><path d="M2 5h20v14H2z M3.5 6.5 12 12.5l8.5-6z" fill-rule="evenodd"/></svg>
          info@northvale.com
        </li>
        <li>
          <svg viewBox="0 0 24 24" aria-hidden="true"><circle cx="12" cy="12" r="10"/></svg>
          www.northvale.com
        </li>
      </ul>
    </div>
  </section>

  <section class="card card--back">
    <div class="brand-name">northvale</div>
  </section>

</div>
</body>
</html>
```